A website for Kovadrel Limited

We need a new and modern website for our company. We are engineering consultants and contractors (EPC) in the oil and gas industry and building services industry.
What we do:
Engineering, procurement, construction
Automation (safety and process)
Non-destructive testing
Training
We have an existing website and the content can be referred from there since we are remaking the website
For more information visit Kovadrel Limited Kenya

```html
<!DOCTYPE html>
<html lang="en">
<head>
<meta charset="utf-8">
<title>Kovadrel Limited</title>
<link href="https://fonts.googleapis.com/css2?family=Lexend:wght@400;500;600&family=Roboto:wght@400;500;700&display=swap" rel="stylesheet">
<style>
:root{
  --orange:#e8531f;
  --orange-2:#f08a2c;
  --dark:#333334;
  --ink:#3a3a3a;
  --text:#666;
  --light:#f3f3f3;
  --white:#fff;
}
*{box-sizing:border-box;margin:0;padding:0}
html,body{width:1200px;height:3942px;overflow:hidden}
body{position:relative;background:var(--white);font-family:Roboto,Arial,sans-serif;color:var(--ink)}
.abs{position:absolute}
header .abs{z-index:10}
.heading{font-family:Lexend,Arial,sans-serif;font-weight:500;font-size:38px;letter-spacing:1px;text-transform:uppercase;color:var(--ink);text-align:center;position:absolute;left:0;width:1200px}
.heading::after{content:"";display:block;width:76px;height:3px;background:var(--orange);margin:8px auto 0}
.btn{position:absolute;display:flex;align-items:center;justify-content:center;gap:8px;border-radius:30px;background:linear-gradient(90deg,var(--orange),var(--orange-2));color:#fff;font-weight:700;font-size:14px;text-transform:uppercase}
.btn .dot{width:12px;height:12px;border-radius:50%;background:#fff;position:relative}
.btn .dot::after{content:"";position:absolute;left:3px;top:3px;border-left:5px solid var(--orange);border-top:3px solid transparent;border-bottom:3px solid transparent}
/* header */
.topline{left:0;top:0;width:1200px;height:4px;background:var(--orange)}
.brand{display:flex;align-items:center;gap:10px}
.brand .mark{width:74px;height:74px;border-radius:50%;border:3px solid var(--orange)}
.brand .name{font-family:Lexend,sans-serif;font-size:22px;line-height:1.25;color:#8a8a8a;text-transform:uppercase;letter-spacing:1px}
.contact-chip{display:flex;align-items:center;gap:14px}
.contact-chip .ic{width:54px;height:54px;border-radius:50%;background:#fff;box-shadow:0 4px 12px rgba(0,0,0,.12);display:flex;align-items:center;justify-content:center}
.contact-chip small{display:block;font-size:11px;color:#888;margin-bottom:4px}
.contact-chip b{font-size:15px;font-weight:500;color:#333}
.cart{left:1052px;top:32px;width:34px;height:34px;border-radius:50%;background:var(--orange);display:flex;align-items:center;justify-content:center;box-shadow:0 0 0 4px #fde0d2}
.navbar{left:431px;top:95px;width:769px;height:50px;background:var(--dark);border-radius:25px 0 0 25px;display:flex;align-items:center;padding-left:40px;gap:24px;font-size:13px;font-weight:700;color:#fff;text-transform:uppercase;white-space:nowrap}
.navbar .active{color:var(--orange-2)}
.navbar .sep{width:1px;height:14px;background:#aaa}
.navbar .soc{width:10px;height:10px;border-radius:50%;background:#fff}
/* hero */
.hero{left:0;top:120px;width:1200px;height:650px;background:linear-gradient(100deg,#5b2a10 0%,#b3521a 35%,#e98a2d 55%,#c45a1c 75%,#7a3410 100%)}
.hero-text{left:598px;top:324px;width:460px;color:#fff}
.hero-text .kicker{font-family:Lexend,sans-serif;font-size:21px;letter-spacing:1px;color:#2d2d2d}
.hero-text h1{font-family:Lexend,sans-serif;font-weight:500;font-size:34px;letter-spacing:1px;color:#2d2d2d;margin-top:4px}
.hero-text p{font-size:16px;line-height:27px;color:#3a2a20;margin-top:18px}
.hero-curve{left:0;top:560px}
.dots{left:564px;top:712px;display:flex;gap:9px}
.dots span{width:11px;height:11px;border-radius:50%;border:1.5px solid #fff}
.dots span.on{background:#fff}
/* about */
.about-title{left:112px;top:910px;font-family:Lexend,sans-serif;font-weight:500;font-size:36px;letter-spacing:1px;color:var(--ink)}
.about-title::after{content:"";display:block;width:76px;height:3px;background:var(--orange);margin-top:6px}
.about-text{left:112px;top:990px;width:473px;font-size:14px;line-height:26px;color:var(--text);text-align:justify}
.ring{left:646px;top:849px;width:444px;height:444px;border-radius:50%;border:8px solid var(--orange);border-left-color:transparent;transform:rotate(-20deg)}
.ring-photo{left:661px;top:864px;width:414px;height:414px;border-radius:50%;background:linear-gradient(180deg,#9b88c4 0%,#c7a3c8 35%,#4c5b7a 60%,#2f3b52 80%,#d9dbe2 100%)}
.badge{left:642px;top:1142px;width:154px;height:154px;border-radius:50%;background:#fff;box-shadow:0 6px 18px rgba(0,0,0,.15);display:flex;align-items:center;justify-content:center}
.badge span{width:96px;height:96px;border-radius:50%;border:3px solid var(--orange)}
/* services */
.services{left:0;top:1397px;width:1200px;height:540px;background:var(--light)}
.card{position:absolute;top:1562px;width:308px;height:300px;background:#fff;border-radius:4px;box-shadow:0 4px 14px rgba(0,0,0,.08);padding:9px}
.card .photo{height:196px;border-radius:2px}
.card .ic{position:absolute;left:119px;top:158px;width:70px;height:70px;border-radius:50%;background:var(--orange);border:5px solid #fff;box-shadow:0 4px 10px rgba(0,0,0,.2);display:flex;align-items:center;justify-content:center}
.card h3{position:absolute;left:0;width:100%;top:256px;text-align:center;font-size:16px;font-weight:500;color:#333;text-transform:uppercase}
.card.featured{background:linear-gradient(180deg,var(--orange),var(--orange-2))}
.card.featured h3{color:#fff}
.card.featured .ic{background:#fff}
.round-arrow{width:34px;height:34px;border-radius:50%;background:#e2e2e2;display:flex;align-items:center;justify-content:center}
/* clients */
.clients{left:0;top:1937px;width:1200px;height:360px;background:linear-gradient(90deg,#dd4a1d,#ec7a2c 60%,#f08d35)}
.client{position:absolute;top:2113px;width:180px;height:95px;background:#fff;display:flex;align-items:center;justify-content:center;font-family:Roboto,sans-serif;font-weight:700;font-size:22px;color:#555}
/* projects */
.tile{position:absolute;border-radius:4px}
/* contact */
.touch{left:0;top:3017px;width:1200px;height:700px;background:var(--light)}
.field{position:absolute;background:#fff;border-radius:3px;font-size:14px;color:#777;padding:14px 17px}
/* footer */
.footer-bg{left:0;top:3460px}
.foot-title{font-size:16px;font-weight:700;color:#fff;text-transform:uppercase}
.foot-title::after{content:"";display:block;width:36px;height:2px;background:var(--orange);margin-top:8px}
.foot-list{list-style:none;font-size:13px;color:#eee}
.foot-list li{display:flex;align-items:flex-start;gap:12px;height:29px}
.bullet{width:11px;height:11px;border-radius:50%;background:var(--orange);position:relative;flex:none;margin-top:2px}
.bullet::after{content:"";position:absolute;left:4px;top:3px;border-left:4px solid var(--dark);border-top:2.5px solid transparent;border-bottom:2.5px solid transparent}
</style>
</head>
<body>

<section>
  <div class="abs hero" role="img" aria-label="Oil pump jack and field engineer at sunset"></div>
  <div class="abs hero-text">
    <div class="kicker">WELCOME TO</div>
    <h1>KOVADREL LIMITED</h1>
    <p>Kovadrel undertakes Design, Supply, Installation and Commissioning of LPG and Petroleum systems including LPG Reticulated Systems.</p>
  </div>
  <div class="btn" style="left:598px;top:517px;width:158px;height:46px">Get Started <span class="dot"></span></div>
  <svg class="abs hero-curve" width="1200" height="220" viewBox="0 0 1200 220">
    <path d="M0 20 Q600 360 1200 0 L1200 220 L0 220 Z" fill="#fff"/>
    <path d="M0 20 Q560 350 1200 10" fill="none" stroke="#e8531f" stroke-width="8"/>
    <path d="M700 180 Q1000 120 1200 0" fill="none" stroke="#f08a2c" stroke-width="5"/>
  </svg>
  <div class="abs dots"><span></span><span class="on"></span><span></span><span></span></div>
</section>

<header>
  <div class="abs topline"></div>
  <div class="abs brand" style="left:125px;top:21px">
    <span class="mark"></span>
    <span class="name">Kovadrel<br>Limited</span>
  </div>
  <div class="abs contact-chip" style="left:580px;top:22px">
    <span class="ic"><svg width="20" height="20" viewBox="0 0 24 24"><path d="M6.6 10.8a15 15 0 006.6 6.6l2.2-2.2c.3-.3.7-.4 1-.2 1.1.4 2.3.6 3.6.6.6 0 1 .4 1 1V20c0 .6-.4 1-1 1A17 17 0 013 4c0-.6.4-1 1-1h3.5c.6 0 1 .4 1 1 0 1.3.2 2.5.6 3.6.1.3 0 .7-.2 1z" fill="#e8531f"/></svg></span>
    <span><small>CALL US:</small><b>+254 700 555 010</b></span>
  </div>
  <div class="abs contact-chip" style="left:802px;top:22px">
    <span class="ic"><svg width="22" height="18" viewBox="0 0 22 18"><rect x="1" y="2" width="20" height="14" rx="2" fill="none" stroke="#e8531f" stroke-width="2"/><path d="M2 3l9 7 9-7" fill="none" stroke="#e8531f" stroke-width="2"/></svg></span>
    <span><small>EMAIL US:</small><b>info@kovadrel.co.ke</b></span>
  </div>
  <div class="abs cart"><svg width="16" height="14" viewBox="0 0 16 14"><path d="M1 1h3l2 8h7l2-6H5" fill="none" stroke="#fff" stroke-width="1.8"/><circle cx="7" cy="12" r="1.3" fill="#fff"/><circle cx="12" cy="12" r="1.3" fill="#fff"/></svg></div>
  <nav class="abs navbar">
    <span class="active">Home</span><span>About Us</span><span>What We Do</span><span>Products</span><span>Our Projects</span><span>Contacts</span>
    <span class="sep"></span><span class="soc" aria-label="Social profile"></span><span class="soc" aria-label="Social profile"></span>
  </nav>
</header>

<section>
  <h2 class="abs about-title">ABOUT US</h2>
  <p class="abs about-text">Kovadrel undertakes Design, Supply, Installation and Commissioning of LPG and Petroleum systems including LPG Reticulated Systems (piped gas). We also do LPG tank revalidation and recertification. Our clients include: Oil companies (both multinationals and local), government agencies, manufacturing companies, agricultural institutions, and the building services industry.</p>
  <div class="btn" style="left:112px;top:1178px;width:152px;height:47px">Read More <span class="dot"></span></div>
  <div class="abs ring"></div>
  <div class="abs ring-photo" role="img" aria-label="Oil refinery with storage tanks at dusk"></div>
  <div class="abs badge"><span></span></div>
</section>

<section>
  <div class="abs services"></div>
  <h2 class="heading" style="top:1462px">What We Do</h2>
  <div class="abs round-arrow" style="left:42px;top:1695px"><svg width="10" height="12"><path d="M7 1L2 6l5 5" fill="none" stroke="#555" stroke-width="2"/></svg></div>
  <div class="abs round-arrow" style="left:1124px;top:1695px"><svg width="10" height="12"><path d="M3 1l5 5-5 5" fill="none" stroke="#555" stroke-width="2"/></svg></div>
  <div class="card" style="left:112px">
    <div class="photo" role="img" aria-label="Technicians working on automated machinery" style="background:linear-gradient(135deg,#6b6f78,#c26a34 55%,#3d4048)"></div>
    <div class="ic"><svg width="34" height="34" viewBox="0 0 34 34"><circle cx="17" cy="17" r="12" fill="none" stroke="#fff" stroke-width="2.5" stroke-dasharray="5 3"/><circle cx="17" cy="17" r="5" fill="none" stroke="#fff" stroke-width="2.5"/></svg></div>
    <h3>Automation</h3>
  </div>
  <div class="card featured" style="left:445px">
    <div class="photo" role="img" aria-label="Engineer inspecting pipeline valves" style="background:linear-gradient(135deg,#d9d4cc,#8d8880 50%,#3a3e48)"></div>
    <div class="ic"><svg width="30" height="30" viewBox="0 0 30 30"><rect x="6" y="3" width="16" height="22" rx="2" fill="none" stroke="#e8531f" stroke-width="2"/><path d="M10 10h8M10 15h8M10 20h5" stroke="#e8531f" stroke-width="2"/><circle cx="22" cy="22" r="4" fill="none" stroke="#e8531f" stroke-width="2"/></svg></div>
    <h3>Non-Destructive Testing</h3>
  </div>
  <div class="card" style="left:779px">
    <div class="photo" role="img" aria-label="Trainee operating industrial equipment" style="background:linear-gradient(135deg,#5a6a80,#9aa2ad 50%,#2f3946)"></div>
    <div class="ic"><svg width="34" height="34" viewBox="0 0 34 34"><circle cx="17" cy="15" r="10" fill="none" stroke="#fff" stroke-width="2.5"/><path d="M13 27h8" stroke="#fff" stroke-width="2.5"/></svg></div>
    <h3>Training</h3>
  </div>
</section>

<section>
  <div class="abs clients" role="img" aria-label="Industrial plant in orange tint"></div>
  <h2 class="heading" style="top:2018px;color:#fff">Our Clients</h2>
  <svg class="abs" style="left:44px;top:2148px" width="16" height="26"><path d="M13 2L3 13l10 11" fill="none" stroke="#fff" stroke-width="3"/></svg>
  <svg class="abs" style="left:1140px;top:2148px" width="16" height="26"><path d="M3 2l10 11L3 24" fill="none" stroke="#fff" stroke-width="3"/></svg>
  <div class="client" style="left:112px">Norvale</div>
  <div class="client" style="left:311px">Tarrex</div>
  <div class="client" style="left:510px">Almira Fuels</div>
  <div class="client" style="left:708px">Bexor</div>
  <div class="client" style="left:907px">Quenta</div>
</section>

<section>
  <h2 class="heading" style="top:2410px">Latest Projects</h2>
  <div class="tile" role="img" aria-label="Engineer at a pipework station" style="left:112px;top:2515px;width:238px;height:179px;background:linear-gradient(135deg,#4a5d74,#9aa7b4 55%,#2c3a4a)"></div>
  <div class="tile" role="img" aria-label="Power plant lit at dusk" style="left:112px;top:2708px;width:238px;height:179px;background:linear-gradient(180deg,#5d7fb0,#b79b7a 55%,#3d3a44)"></div>
  <div class="tile" role="img" aria-label="Two engineers reviewing a laptop at an oil field" style="left:364px;top:2515px;width:471px;height:372px;background:linear-gradient(180deg,#5a93cc 0%,#b6d3ea 35%,#d9893c 60%,#5a5142 100%)"></div>
  <div class="tile" role="img" aria-label="Pipeline rows with yellow valves" style="left:848px;top:2515px;width:240px;height:179px;background:linear-gradient(180deg,#c9ced6,#7b8088 55%,#2d3036)"></div>
  <div class="tile" role="img" aria-label="Engineers studying plans on site" style="left:848px;top:2708px;width:240px;height:179px;background:linear-gradient(135deg,#e7c860,#c9cbd0 45%,#d0562c)"></div>
</section>

<section>
  <div class="abs touch"></div>
  <h2 class="heading" style="top:3092px">Get In Touch</h2>
  <div class="field" style="left:165px;top:3184px;width:282px;height:49px">Full Name</div>
  <div class="field" style="left:459px;top:3184px;width:282px;height:49px">Phone Number</div>
  <div class="field" style="left:751px;top:3184px;width:283px;height:49px">Email Address</div>
  <div class="field" style="left:165px;top:3245px;width:869px;height:92px">Message...!</div>
  <div class="btn" style="left:519px;top:3355px;width:162px;height:49px">Send Message</div>
</section>

<footer>
  <svg class="abs footer-bg" width="1200" height="482" viewBox="0 0 1200 482">
    <path d="M0 210 Q600 -90 1200 210 L1200 482 L0 482 Z" fill="#333334"/>
    <path d="M0 200 Q600 -110 1200 200" fill="none" stroke="#e8531f" stroke-width="7"/>
  </svg>
  <div class="abs brand" style="left:502px;top:3556px">
    <span class="mark" style="border-color:#fff;width:76px;height:76px"></span>
    <span class="name" style="color:#fff">Kovadrel<br>Limited</span>
  </div>
  <div class="abs" style="left:994px;top:3658px;font-size:14px;font-weight:700;color:#fff">GO TO TOP <span style="color:var(--orange)">&#8593;</span></div>

  <div class="abs" style="left:110px;top:3698px">
    <div class="foot-title">Contact Info</div>
    <ul class="foot-list" style="margin-top:22px">
      <li style="height:56px"><svg width="10" height="14" viewBox="0 0 10 14"><path d="M5 0a5 5 0 00-5 5c0 4 5 9 5 9s5-5 5-9a5 5 0 00-5-5z" fill="#e8531f"/><circle cx="5" cy="5" r="1.8" fill="#333334"/></svg><span>Tendo Court, Suite C14,<br><span style="display:block;margin-top:4px">Harbour Road</span></span></li>
      <li><svg width="12" height="12" viewBox="0 0 24 24"><path d="M6.6 10.8a15 15 0 006.6 6.6l2.2-2.2c.3-.3.7-.4 1-.2 1.1.4 2.3.6 3.6.6.6 0 1 .4 1 1V20c0 .6-.4 1-1 1A17 17 0 013 4c0-.6.4-1 1-1h3.5c.6 0 1 .4 1 1 0 1.3.2 2.5.6 3.6.1.3 0 .7-.2 1z" fill="#e8531f"/></svg><span>+254 700 555 010 | +254 700 555 024</span></li>
      <li><svg width="13" height="10" viewBox="0 0 13 10"><rect width="13" height="10" rx="1" fill="#e8531f"/><path d="M0 1l6.5 5L13 1" fill="none" stroke="#333334" stroke-width="1.2"/></svg><span>info@kovadrel.co.ke</span></li>
    </ul>
  </div>

  <div class="abs" style="left:436px;top:3698px">
    <div class="foot-title">Quick Links</div>
    <ul class="foot-list" style="margin-top:22px">
      <li><span class="bullet"></span>Home</li>
      <li><span class="bullet"></span>About Us</li>
      <li><span class="bullet"></span>What We Do</li>
      <li><span class="bullet"></span>Products</li>
    </ul>
  </div>
  <ul class="abs foot-list" style="left:676px;top:3750px">
    <li><span class="bullet"></span>Our Projects</li>
    <li><span class="bullet"></span>Contact Us</li>
    <li><span class="bullet"></span>Privacy Policy</li>
    <li><span class="bullet"></span>Terms &amp; Conditions</li>
  </ul>

  <div class="abs" style="left:933px;top:3698px">
    <div class="foot-title">Follow Us</div>
    <div style="display:flex;gap:10px;margin-top:22px">
      <span style="width:34px;height:34px;border-radius:50%;background:var(--orange)" aria-label="Social profile"></span>
      <span style="width:34px;height:34px;border-radius:50%;background:#fff" aria-label="Social profile"></span>
    </div>
  </div>

  <div class="abs" style="left:110px;top:3886px;width:978px;height:1px;background:#4a4a4b"></div>
  <div class="abs" style="left:0;top:3904px;width:1200px;text-align:center;font-size:13px;color:#eee">© 2023 KOVADREL LIMITED &nbsp;&nbsp;|&nbsp;&nbsp; All Rights Reserved</div>
</footer>

</body>
</html>
```